ULMIRA card Technical Architecture

Hello everyone ULMIRA: It is a consulting firm in Architecture and Construction. I require a card duplexing, sober, elegant, classic but not boring. Update 1: Use the following data for the card. Name: Gonzalo Pereda Mauricio Villalta Position: COO Twitter: @ulmiraAT Homepage: ulmira-example.com home address not include the participation of all thank you.

Target Market(s)

Construction companies, Architects and Consulting Engineers

Industry/Entity Type

Consulting

Contact Information for Business Card

Los campos que debe tener:
Nombre, Cargo, email, homepage y twitter

Font styles to use
Serif
Sans Serif
Other font styles liked:
• Me gustan playfair display, open sans y roboto, pero estoy sujeto a sus propuestas

Requirements
Must have
• Colors: Present combined proposals in white, red, gray and black Update 1: The two names must be clearly differentiated from the two surnames
Nice to have
• They are free to present their best proposals. I will bring them immediate feedback to the extent you can go see their designs. Complete data for card and logo files will give the winner the

```html
<!DOCTYPE html>
<html lang="es">
<head>
<meta charset="utf-8">
<title>ULMIRA – Arquitectura Técnica business card</title>
<link rel="stylesheet" href="https://fonts.googleapis.com/css2?family=Open+Sans:wght@400;600;700&family=Raleway:wght@400;500&display=swap">
<style>
  :root {
    --red: #bf0000;
    --black: #000000;
    --white: #ffffff;
    --gray-rule: #8a8a8a;
    --backdrop: #e9e7e4;
    --ink: #111111;
  }
  * { margin: 0; padding: 0; box-sizing: border-box; }
  html, body {
    width: 1200px; height: 900px; overflow: hidden;
    background: var(--backdrop);
  }
  .canvas { position: relative; width: 1200px; height: 900px; }

  .card { position: absolute; overflow: hidden; box-shadow: 0 6px 18px rgba(0,0,0,.18); }

  /* Front */
  .card-front { left: 78px; top: 34px; width: 588px; height: 364px; background: var(--white); }
  .card-front .bands { position: absolute; inset: 0; }
  .brand-front {
    position: absolute; left: 0; width: 588px; top: 72px; text-align: center;
  }
  .brand-name {
    font-family: "Raleway", sans-serif; font-weight: 400;
    letter-spacing: 0.22em; line-height: 1; color: var(--ink);
  }
  .brand-front .brand-name { font-size: 40px; padding-left: 0.22em; }
  .brand-rule { height: 1px; background: var(--gray-rule); margin: 0 auto; }
  .brand-front .brand-rule { width: 336px; margin-top: 8px; }
  .tagline {
    font-family: "Raleway", sans-serif; font-weight: 500;
    color: var(--red); text-transform: uppercase; line-height: 1;
  }
  .brand-front .tagline { font-size: 15px; letter-spacing: 0.19em; margin-top: 6px; padding-left: 0.19em; }

  .person {
    position: absolute; right: 308px; top: 275px; text-align: right;
    font-family: "Open Sans", sans-serif; color: var(--white);
  }
  .person-name { font-size: 19px; font-weight: 700; line-height: 1.2; text-transform: uppercase; letter-spacing: -0.01em; }
  .person-role { font-size: 15.5px; font-weight: 400; line-height: 1.4; }
  .divider {
    position: absolute; left: 294px; top: 280px; width: 1px; height: 36px;
    background: rgba(255,255,255,.75);
  }
  .contact {
    position: absolute; left: 307px; top: 277px; list-style: none;
    font-family: "Open Sans", sans-serif; font-size: 15.5px; color: var(--white);
  }
  .contact li { display: flex; align-items: center; height: 22px; }
  .contact svg { width: 11px; height: 11px; margin-right: 8px; flex: none; }

  /* Back */
  .card-back { left: 388px; top: 505px; width: 567px; height: 352px; background: var(--black); }
  .brand-back { position: absolute; left: 0; width: 567px; top: 186px; text-align: center; }
  .brand-back .brand-name { color: var(--white); font-size: 48px; letter-spacing: 0.28em; padding-left: 0.28em; }
  .brand-back .brand-rule { width: 400px; background: #5a1010; margin-top: 8px; }
  .brand-back .tagline { font-size: 17px; letter-spacing: 0.25em; margin-top: 8px; padding-left: 0.25em; }
  .social { position: absolute; left: 254px; top: 297px; display: flex; gap: 17px; }
  .social span { width: 20px; height: 20px; background: var(--red); display: block; }
</style>
</head>
<body>
<main class="canvas">

  <section class="card card-front" aria-label="Business card front">
    <svg class="bands" width="588" height="364" viewBox="0 0 588 364" aria-hidden="true">
      <polygon points="0,200 400,200 379,224 0,224" fill="var(--black)"/>
      <polygon points="0,228 383,228 414,191 588,191 588,364 0,364" fill="var(--red)"/>
    </svg>

    <div class="brand-front">
      <div class="brand-name">ULMIRA</div>
      <div class="brand-rule"></div>
      <div class="tagline">Arquitectura Técnica</div>
    </div>

    <div class="person">
      <p class="person-name">Tomás Ruelas</p>
      <p class="person-role">Managing Director</p>
    </div>
    <div class="divider"></div>
    <ul class="contact">
      <li>
        <svg viewBox="0 0 11 11" aria-hidden="true"><rect x="2.5" y="0.5" width="6" height="10" rx="1" fill="none" stroke="#fff" stroke-width="1.2"/><rect x="4.5" y="8" width="2" height="1" fill="#fff"/></svg>
        (044)555010203
      </li>
      <li>
        <svg viewBox="0 0 11 11" aria-hidden="true"><rect x="0.5" y="2" width="10" height="7" fill="#fff"/><polyline points="0.5,2 5.5,6 10.5,2" fill="none" stroke="var(--red)" stroke-width="1"/></svg>
        info@ulmira-example.com
      </li>
    </ul>
  </section>

  <section class="card card-back" aria-label="Business card back">
    <div class="brand-back">
      <div class="brand-name">ULMIRA</div>
      <div class="brand-rule"></div>
      <div class="tagline">Arquitectura Técnica</div>
    </div>
    <div class="social" aria-hidden="true"><span></span><span></span></div>
  </section>

</main>
</body>
</html>
```